New PowerPoint Brelta Project

I need a company powerpoint template for my company, Varnok (see Brelta file logo attached), that has a number of templated slides with an exciting supporting colour palette. Needs to have header and footer sections, tables in colour which support the logo colour, bar and line charts, dot point slides and image (placeholders) slides. Logo is attached.
The primary use of this template is to pitch for new work - ie about us page, previous clients page, then a breakdown of services offered in a table format with prices etc...
Updates

Hi everyone
Please see some example PPT templates that provide more of a guide as to what I need.

Thanks
Leopold

Font styles to use
Serif
Sans Serif

Colors
0054AA
0677BA
7BADD7
CADEEF
E8F1F8
00AB8E
00BBA5
67D7C9
C6EFE9
E9F9F6
59FF00
82FF00
B8FF75
E3FFCB
F4FFEA
FFC000
F8CF3A
FAE287
FDF2CF
FEFAEE

```html
<!DOCTYPE html>
<html lang="en">
<head>
<meta charset="utf-8">
<title>Varnok — Presentation Template</title>
<link href="https://fonts.googleapis.com/css2?family=Cinzel:wght@400;600;700&family=Poppins:wght@400;500;600&display=swap" rel="stylesheet">
<style>
:root{
  --canvas:#6fada3;
  --slide:#0d3b30;
  --gold:#e3b53c;
  --gold-deep:#d9a92c;
  --pale:#f4dd91;
  --pale-line:#c9ad5a;
  --ink:#1d2a24;
  --white:#ffffff;
  --bar:#1d5e52;
  --bar-top:#2d7c6d;
  --bar-side:#174d43;
}
*{box-sizing:border-box;margin:0;padding:0}
html,body{width:1200px;height:347px;overflow:hidden;background:var(--canvas)}
body{position:relative;font-family:'Poppins',sans-serif;color:var(--white)}
.slide{position:absolute;width:292px;height:164px;background:var(--slide);overflow:hidden}
.s1{left:7px;top:7px}.s2{left:305px;top:7px}.s3{left:602px;top:7px}.s4{left:900px;top:7px}
.s5{left:7px;top:178px}.s6{left:305px;top:178px}.s7{left:602px;top:178px}.s8{left:900px;top:178px}
.abs{position:absolute}
.brand{position:absolute;right:6px;top:3px;font-family:'Cinzel',serif;font-size:14px;color:var(--gold);letter-spacing:.3px}
.title{position:absolute;font-family:'Cinzel',serif;font-weight:700;font-size:9px;letter-spacing:.2px;color:var(--white)}
.title.center{text-align:center}
.rule{position:absolute;height:1.5px;width:22px;background:var(--gold)}
.footer{position:absolute;left:0;right:0;bottom:5px;text-align:center;font-size:4.4px;color:var(--gold)}
.page{position:absolute;right:10px;bottom:4px;font-size:4.4px;color:var(--white)}
.body-text{position:absolute;font-size:3.4px;line-height:5.3px;color:var(--white)}
.photo{position:absolute}

.cover-photo{inset:0;background:linear-gradient(180deg,#365d54 0%,#2c5249 55%,#24473f 100%)}
.cover-name{position:absolute;left:0;width:292px;top:42px;text-align:center;font-family:'Cinzel',serif;font-size:36px;color:var(--gold);letter-spacing:1px}
.socials{position:absolute;left:116px;top:92px;display:flex;gap:8px}
.socials span{width:13px;height:13px;border-radius:50%;background:var(--gold)}

.toc{position:absolute;left:173px;top:30px;width:106px;list-style:none}
.toc li{display:flex;justify-content:space-between;font-size:5.3px;font-weight:500;height:13.8px}
.toc b{font-weight:600;margin-right:2px}

.clients{position:absolute;left:16px;top:64px;display:grid;grid-template-columns:repeat(4,59px);grid-auto-rows:27px;gap:8px 7px}
.client{border:1px solid var(--gold);border-radius:2px;display:flex;align-items:center;justify-content:center;gap:3px;font-size:8px;font-weight:500;color:var(--gold)}
.client i{width:5px;height:5px;background:var(--gold)}

.price-table{position:absolute;left:16px;top:39px;width:260px;border-collapse:collapse;font-size:3.6px;color:var(--ink);background:var(--pale)}
.price-table th{background:var(--gold-deep);font-weight:600;height:9px;border:.5px solid var(--pale-line)}
.price-table td{height:9.1px;text-align:center;border:.5px solid var(--pale-line)}
.price-table svg{width:5px;height:5px;vertical-align:middle}

.process-frame{left:14px;top:38px;width:125px;height:103px;border:1px solid var(--gold);padding:3px}
.process-photo{width:100%;height:100%;background:linear-gradient(135deg,#5b5f60,#2a2d2e 60%,#1b1d1e)}
.steps{position:absolute;left:150px;top:38px;list-style:none}
.steps li{display:flex;align-items:center;height:21.5px;gap:5px}
.steps .num{width:17px;height:17px;border:1px solid var(--gold);border-radius:50%;display:flex;align-items:center;justify-content:center;font-family:'Cinzel',serif;font-weight:700;font-size:6.5px;color:var(--gold)}
.steps p{font-size:3.7px;line-height:5.8px;width:100px}

.chart{position:absolute;top:46px;height:82px}
.chart.bars{left:13px;width:155px;background:var(--gold)}
.chart.line{left:176px;width:104px;background:var(--pale)}
.chart svg{width:100%;height:100%}
.chart text{font-family:'Poppins',sans-serif;fill:var(--ink)}

.contact-photo{left:0;top:0;width:141px;height:164px;background:linear-gradient(180deg,#9fb9c9 0%,#b9c9d1 45%,#6f767a 75%,#3e4244 100%)}
.contacts{position:absolute;left:158px;top:66px;list-style:none}
.contacts li{display:flex;align-items:flex-start;gap:5px;font-size:4.9px;font-weight:600;line-height:8px;margin-bottom:7px}
.contacts .icon{flex:none;width:12px;height:12px;border-radius:2px;background:var(--gold);display:flex;align-items:center;justify-content:center}
.contacts .icon svg{width:7px;height:7px}
.contacts .text{padding-top:2px;width:100px}
</style>
</head>
<body>

<svg width="0" height="0" style="position:absolute" aria-hidden="true">
  <symbol id="tick" viewBox="0 0 10 10"><circle cx="5" cy="5" r="4.2" fill="none" stroke="#2f3a34" stroke-width=".8"/><path d="M3 5.2l1.4 1.4L7.2 3.7" fill="none" stroke="#2f3a34" stroke-width=".9"/></symbol>
  <symbol id="cross" viewBox="0 0 10 10"><path d="M2 2l6 6M8 2L2 8" stroke="#1d2a24" stroke-width="1.2"/></symbol>
</svg>

<section class="slide s1">
  <div class="photo cover-photo" role="img" aria-label="Photo of a grey sports coupe under a dark green overlay"></div>
  <div class="cover-name">VARNOK</div>
  <div class="socials" aria-label="Social profiles"><span></span><span></span><span></span></div>
  <div class="footer">© 2025 Varnok | All Rights Reserved</div>
</section>

<section class="slide s2">
  <div class="brand">VARNOK</div>
  <h2 class="title" style="left:10px;top:33px">CONTENT PRESENTATION</h2>
  <p class="body-text" style="left:10px;top:52px;width:136px">Lorem Ipsum is simply dummy text of the printing and typesetting industry. Lorem Ipsum has been the industry's standard dummy text ever since the 1500s, when an unknown printer took a galley of type and scrambled it to make a type specimen book. It has survived not only five centuries, but also the leap into electronic typesetting, remaining essentially unchanged. It was popularised in the 1960s with the release of Pressmark sheets containing Lorem Ipsum passages, and more recently with desktop publishing software like Folio Layout including versions of Lorem Ipsum.</p>
  <ol class="toc">
    <li><span><b>01.</b> Introduction</span><span>03</span></li>
    <li><span><b>02.</b> Why Regular Car Service</span><span>04</span></li>
    <li><span><b>03.</b> Types of Car Services</span><span>05</span></li>
    <li><span><b>04.</b> Our Services</span><span>06</span></li>
    <li><span><b>05.</b> Our Process</span><span>07</span></li>
    <li><span><b>06.</b> Gallery</span><span>08</span></li>
    <li><span><b>07.</b> Why Choose Us?</span><span>09</span></li>
    <li><span><b>08.</b> Contact Us</span><span>10</span></li>
  </ol>
</section>

<section class="slide s3">
  <div class="brand">VARNOK</div>
  <h2 class="title" style="left:10px;top:30px">CONTENT PRESENTATION</h2>
  <div class="rule" style="left:10px;top:42px"></div>
  <p class="body-text" style="left:10px;top:52px;width:130px;line-height:6.8px">Lorem Ipsum is simply dummy text of the printing and typesetting industry. Lorem Ipsum has been the industry's standard dummy text ever since the 1500s, when an unknown printer took a galley of type and scrambled it to make a type specimen book. It has survived not only five centuries, but also the leap into electronic typesetting, remaining essentially unchanged.<br>It was popularised in the 1960s with the release of Pressmark sheets containing Lorem Ipsum passages, and more recently with desktop publishing software like Folio Layout including versions of Lorem Ipsum.</p>
  <div class="photo" role="img" aria-label="Sunset sky behind the vehicle" style="left:218px;top:34px;width:64px;height:96px;background:linear-gradient(180deg,#3d5a7a,#c98a4a 60%,#e6a14a)"></div>
  <div class="photo" role="img" aria-label="Photo of a red luxury SUV at sunset" style="left:150px;top:46px;width:116px;height:88px;background:linear-gradient(160deg,#6a5040,#8a2a26 45%,#3a1c1a 80%,#2a2a2a)"></div>
  <div class="footer">© 2025 Varnok | All Rights Reserved</div>
  <div class="page">03</div>
</section>

<section class="slide s4">
  <div class="brand">VARNOK</div>
  <h2 class="title center" style="top:12px;left:0;width:292px">PREVIOUS CLIENTS</h2>
  <div class="rule" style="left:135px;top:26px"></div>
  <p class="body-text" style="left:40px;top:34px;width:212px;text-align:center;line-height:6.8px">Lorem Ipsum is simply dummy text of the printing and typesetting industry. Lorem Ipsum has been the industry's standard dummy text ever since the 1500s, when an unknown printer took a galley of type and scrambled it to make a type specimen book.</p>
  <div class="clients">
    <div class="client"><i></i>Brelta</div>
    <div class="client">Quillon</div>
    <div class="client">Tarvex</div>
    <div class="client">Orvane</div>
    <div class="client"><i></i>Brelta</div>
    <div class="client">Quillon</div>
    <div class="client">Tarvex</div>
    <div class="client">Nestly</div>
  </div>
  <div class="footer">© 2025 Varnok | All Rights Reserved</div>
  <div class="page">04</div>
</section>

<section class="slide s5">
  <div class="brand">VARNOK</div>
  <h2 class="title center" style="top:12px;left:-15px;width:290px">OUR SERVICES</h2>
  <div class="rule" style="left:119px;top:26px"></div>
  <table class="price-table">
    <thead><tr><th>Service / Package</th><th>Basic</th><th>Standard</th><th>Professional</th><th>Ultimate</th><th>Developer</th></tr></thead>
    <tbody>
      <tr><td>Price</td><td>$25</td><td>$35</td><td>$45</td><td>$55</td><td>$65</td></tr>
      <tr><td>Lorem Ipsum</td><td><svg><use href="#tick"/></svg></td><td><svg><use href="#tick"/></svg></td><td><svg><use href="#tick"/></svg></td><td><svg><use href="#tick"/></svg></td><td><svg><use href="#tick"/></svg></td></tr>
      <tr><td>Lorem Ipsum</td><td><svg><use href="#tick"/></svg></td><td><svg><use href="#tick"/></svg></td><td><svg><use href="#tick"/></svg></td><td><svg><use href="#tick"/></svg></td><td><svg><use href="#tick"/></svg></td></tr>
      <tr><td>Lorem Ipsum</td><td><svg><use href="#tick"/></svg></td><td><svg><use href="#tick"/></svg></td><td><svg><use href="#tick"/></svg></td><td><svg><use href="#tick"/></svg></td><td><svg><use href="#tick"/></svg></td></tr>
      <tr><td>Lorem Ipsum</td><td><svg><use href="#tick"/></svg></td><td><svg><use href="#tick"/></svg></td><td><svg><use href="#tick"/></svg></td><td><svg><use href="#tick"/></svg></td><td><svg><use href="#tick"/></svg></td></tr>
      <tr><td>Lorem Ipsum</td><td><svg><use href="#cross"/></svg></td><td><svg><use href="#cross"/></svg></td><td><svg><use href="#cross"/></svg></td><td><svg><use href="#tick"/></svg></td><td><svg><use href="#tick"/></svg></td></tr>
      <tr><td>Lorem Ipsum</td><td><svg><use href="#cross"/></svg></td><td><svg><use href="#cross"/></svg></td><td><svg><use href="#cross"/></svg></td><td><svg><use href="#tick"/></svg></td><td><svg><use href="#tick"/></svg></td></tr>
      <tr><td>Lorem Ipsum</td><td><svg><use href="#cross"/></svg></td><td><svg><use href="#cross"/></svg></td><td><svg><use href="#cross"/></svg></td><td><svg><use href="#tick"/></svg></td><td><svg><use href="#tick"/></svg></td></tr>
      <tr><td>Lorem Ipsum</td><td><svg><use href="#cross"/></svg></td><td><svg><use href="#cross"/></svg></td><td><svg><use href="#cross"/></svg></td><td><svg><use href="#cross"/></svg></td><td><svg><use href="#tick"/></svg></td></tr>
      <tr><td>Lorem Ipsum</td><td><svg><use href="#cross"/></svg></td><td><svg><use href="#cross"/></svg></td><td><svg><use href="#cross"/></svg></td><td><svg><use href="#cross"/></svg></td><td><svg><use href="#tick"/></svg></td></tr>
    </tbody>
  </table>
  <div class="footer">© 2025 Varnok | All Rights Reserved</div>
  <div class="page">05</div>
</section>

<section class="slide s6">
  <div class="brand">VARNOK</div>
  <h2 class="title center" style="top:12px;left:-15px;width:290px">OUR PROCESS</h2>
  <div class="rule" style="left:119px;top:26px"></div>
  <div class="abs process-frame"><div class="process-photo" role="img" aria-label="Black and white photo of a dark sports car, front view"></div></div>
  <ol class="steps">
    <li><span class="num">01</span><p>Lorem Ipsum is simply dummy text of the printing and typesetting industry.</p></li>
    <li><span class="num">02</span><p>Lorem Ipsum is simply dummy text of the printing and typesetting industry.</p></li>
    <li><span class="num">03</span><p>Lorem Ipsum is simply dummy text of the printing and typesetting industry.</p></li>
    <li><span class="num">04</span><p>Lorem Ipsum is simply dummy text of the printing and typesetting industry.</p></li>
    <li><span class="num">05</span><p>Lorem Ipsum is simply dummy text of the printing and typesetting industry.</p></li>
  </ol>
  <div class="footer">© 2025 Varnok | All Rights Reserved</div>
  <div class="page">06</div>
</section>

<section class="slide s7">
  <div class="brand">VARNOK</div>
  <h2 class="title center" style="top:12px;left:-15px;width:290px">TABLE</h2>
  <div class="rule" style="left:119px;top:26px"></div>
  <div class="chart bars">
    <svg viewBox="0 0 155 82" aria-label="Bar chart 2018 to 2022">
      <text x="4" y="8" font-size="3">Lorem</text>
      <g font-size="2.8" text-anchor="end">
        <text x="10" y="15">700</text><text x="10" y="22.5">600</text><text x="10" y="29.5">500</text><text x="10" y="36.5">400</text><text x="10" y="43.5">300</text><text x="10" y="50.5">200</text><text x="10" y="57.5">100</text><text x="10" y="65">0</text>
      </g>
      <g>
        <rect x="20" y="30" width="15" height="34" fill="var(--bar)"/><polygon points="20,30 23,28 38,28 35,30" fill="var(--bar-top)"/><rect x="35" y="28" width="3" height="36" fill="var(--bar-side)"/>
        <rect x="47" y="28.5" width="15" height="35.5" fill="var(--bar)"/><polygon points="47,28.5 50,26.5 65,26.5 62,28.5" fill="var(--bar-top)"/><rect x="62" y="26.5" width="3" height="37.5" fill="var(--bar-side)"/>
        <rect x="74" y="30.5" width="15" height="33.5" fill="var(--bar)"/><polygon points="74,30.5 77,28.5 92,28.5 89,30.5" fill="var(--bar-top)"/><rect x="89" y="28.5" width="3" height="35.5" fill="var(--bar-side)"/>
        <rect x="101" y="22.5" width="15" height="41.5" fill="var(--bar)"/><polygon points="101,22.5 104,20.5 119,20.5 116,22.5" fill="var(--bar-top)"/><rect x="116" y="20.5" width="3" height="43.5" fill="var(--bar-side)"/>
        <rect x="128" y="18.5" width="15" height="45.5" fill="var(--bar)"/><polygon points="128,18.5 131,16.5 146,16.5 143,18.5" fill="var(--bar-top)"/><rect x="143" y="16.5" width="3" height="47.5" fill="var(--bar-side)"/>
      </g>
      <g font-size="2.8" text-anchor="middle">
        <text x="28" y="24.5">473</text><text x="55" y="23">495</text><text x="82" y="25">466</text><text x="109" y="17">579</text><text x="136" y="13">632</text>
        <text x="28" y="70">2018</text><text x="55" y="70">2019</text><text x="82" y="70">2020</text><text x="109" y="70">2021</text><text x="136" y="70">2022</text>
      </g>
    </svg>
  </div>
  <div class="chart line">
    <svg viewBox="0 0 104 82" aria-label="Line chart October to June">
      <text x="52" y="6" font-size="3" text-anchor="middle">Lorem Ipsum is simply dummy</text>
      <text x="52" y="10" font-size="3" text-anchor="middle">text of the printing and typesetting</text>
      <text x="52" y="14" font-size="3" text-anchor="middle">industry.</text>
      <g font-size="2.6" text-anchor="end">
        <text x="7" y="12">90</text><text x="7" y="19">80</text><text x="7" y="25">70</text><text x="7" y="31.5">60</text><text x="7" y="38">50</text><text x="7" y="44.5">40</text><text x="7" y="51">30</text><text x="7" y="57.5">20</text><text x="7" y="64">10</text><text x="7" y="70.5">0</text>
      </g>
      <g stroke="#8a8f7a" stroke-width=".3"><line x1="10" y1="30.5" x2="100" y2="30.5"/><line x1="10" y1="43.5" x2="100" y2="43.5"/><line x1="10" y1="63" x2="100" y2="63"/><line x1="10" y1="69.5" x2="100" y2="69.5"/></g>
      <polyline points="10,47 21,28.5 30,51 40,48.5 50,40.5 60,63 70,54 85,25" fill="none" stroke="#1d2a24" stroke-width=".5"/>
      <circle cx="21" cy="28.5" r="1.3" fill="var(--bar)"/><circle cx="60" cy="63" r="1.3" fill="var(--bar)"/>
      <g font-size="2.6" text-anchor="middle">
        <text x="10" y="74.5">Oct</text><text x="20" y="74.5">Nov</text><text x="29" y="74.5">Dec</text><text x="38" y="74.5">Jan</text><text x="48" y="74.5">Feb</text><text x="58" y="74.5">Mar</text><text x="67" y="74.5">Apr</text><text x="77" y="74.5">May</text><text x="86" y="74.5">Jun</text>
      </g>
    </svg>
  </div>
  <div class="footer">© 2025 Varnok | All Rights Reserved</div>
  <div class="page">07</div>
</section>

<section class="slide s8">
  <div class="photo contact-photo" role="img" aria-label="Photo of a silver sports coupe on an open road"></div>
  <div class="brand">VARNOK</div>
  <h2 class="title" style="left:158px;top:40px">CONTACT US</h2>
  <div class="rule" style="left:158px;top:53px"></div>
  <ul class="contacts">
    <li><span class="icon"><svg viewBox="0 0 10 10"><path d="M2.2 1.2l1.6-.2 1 2.3-1 .8a5 5 0 0 0 2.3 2.3l.8-1 2.3 1-.2 1.6C6.5 8.5 1.5 3.5 2.2 1.2z" fill="#0d3b30"/></svg></span><span class="text">+1555 010 2040</span></li>
    <li><span class="icon"><svg viewBox="0 0 10 10"><rect x="1" y="2.5" width="8" height="5.5" fill="#0d3b30"/><path d="M1 2.5l4 3 4-3" fill="none" stroke="#e3b53c" stroke-width=".6"/></svg></span><span class="text">admin@varnok.com</span></li>
    <li><span class="icon"><svg viewBox="0 0 10 10"><path d="M5 9.5S2 6 2 4a3 3 0 0 1 6 0c0 2-3 5.5-3 5.5z" fill="#0d3b30"/><circle cx="5" cy="4" r="1.1" fill="#e3b53c"/></svg></span><span class="text">Lorem Ipsum is simply dummy text of the printing and typesetting industry.</span></li>
  </ul>
</section>

</body>
</html>
```